Weightloss company needs Business Card

We want a business card that is clean and professional, yet portrays that we are a friendly, innovative, and versatile program designed to fit the needs of our clients.
I would like there to be 2 sides, one side having an appointment card, and the other side containing the logo and business information. There can be decorations on both sides. The logo is attached.

Target Market(s)

Men and women 40-60

Industry/Entity Type

Business

Contact Information for Business Card

Font styles to use
Sans Serif

Requirements
Must have
• The logo, space for business information
Nice to have
• The colors in the logo
Should not have
• No pictures of people or food

```html
<!DOCTYPE html>
<html lang="en">
<head>
<meta charset="utf-8">
<title>Turnwell Weightloss — Business Card</title>
<link href="https://fonts.googleapis.com/css2?family=Open+Sans:wght@400;600;800&display=swap" rel="stylesheet">
<style>
  :root {
    --stage: #3a332f;
    --card-dark: #111112;
    --card-light: #f1f1f1;
    --brand-red: #e1163c;
    --ink-light: #f4f4f4;
    --ink-dark: #1a1a1a;
    --rule-dark: #3a3a3c;
  }
  * { box-sizing: border-box; margin: 0; padding: 0; }
  html, body {
    width: 1200px; height: 844px; overflow: hidden;
    background: var(--stage);
    font-family: "Open Sans", Arial, sans-serif;
  }
  .stage {
    width: 1200px; height: 844px;
    display: flex; align-items: center; justify-content: center; gap: 50px;
  }
  .card {
    width: 520px; height: 300px; border-radius: 4px;
    position: relative;
    box-shadow: 0 10px 26px rgba(0,0,0,.45);
  }
  /* brand name in place of the mark */
  .brand {
    display: flex; align-items: center; justify-content: center; gap: 8px;
    color: var(--brand-red);
    font-weight: 800;
  }
  .brand-dot {
    width: 14px; height: 14px; border-radius: 50%;
    background: var(--brand-red);
  }

  /* Front: contact card */
  .card-front { background: var(--card-dark); color: var(--ink-light); }
  .card-front .brand { position: absolute; top: 70px; left: 0; right: 0; font-size: 28px; }
  .details {
    position: absolute; top: 150px; left: 40px; right: 30px;
    display: flex; align-items: stretch;
  }
  .person { flex: 1; text-align: right; padding-right: 22px; padding-top: 10px; }
  .person-name { color: var(--brand-red); font-size: 21px; font-weight: 400; line-height: 1.15; }
  .person-role { font-size: 14px; margin-bottom: 14px; }
  .person-address { font-size: 15px; line-height: 1.2; }
  .divider { width: 1px; background: var(--rule-dark); }
  .contacts { list-style: none; padding-left: 18px; font-size: 14px; }
  .contacts li { display: flex; align-items: center; gap: 10px; line-height: 23px; }
  .contacts svg { width: 12px; height: 12px; fill: var(--brand-red); flex: none; }

  /* Back: appointment card */
  .card-back { background: var(--card-light); color: var(--brand-red); padding: 34px 34px 0; }
  .card-back .brand { font-size: 22px; margin-bottom: 22px; }
  .appt-title { text-align: center; font-size: 19px; font-weight: 600; margin-bottom: 6px; }
  .blank-line { border-bottom: 2px dotted var(--ink-dark); height: 22px; margin-left: 40px; }
  .field { display: flex; align-items: flex-end; font-size: 13px; margin-top: 10px; }
  .field-label { flex: none; margin-right: 6px; }
  .field-fill { flex: 1; border-bottom: 2px dotted var(--ink-dark); height: 12px; }
  .field-unit { color: var(--ink-dark); font-size: 12px; font-weight: 600; margin: 0 2px; }
  .notice { font-size: 12.5px; margin-top: 14px; }
</style>
</head>
<body>
<main class="stage">

  <section class="card card-front" aria-label="Contact side">
    <div class="brand"><span class="brand-dot"></span>Turnwell Weightloss</div>
    <div class="details">
      <div class="person">
        <p class="person-name">Daniel Harper</p>
        <p class="person-role">Managing Director</p>
        <p class="person-address">12345, Address Goes Here<br>Country Name, 123456</p>
      </div>
      <div class="divider"></div>
      <ul class="contacts">
        <li><svg viewBox="0 0 24 24"><path d="M6.6 10.8a15 15 0 0 0 6.6 6.6l2.2-2.2a1 1 0 0 1 1-.25 11.4 11.4 0 0 0 3.6.6 1 1 0 0 1 1 1V20a1 1 0 0 1-1 1A17 17 0 0 1 3 4a1 1 0 0 1 1-1h3.5a1 1 0 0 1 1 1c0 1.25.2 2.45.6 3.6a1 1 0 0 1-.25 1z"/></svg>(044)-555-0142</li>
        <li><svg viewBox="0 0 24 24"><path d="M7 1h10a2 2 0 0 1 2 2v18a2 2 0 0 1-2 2H7a2 2 0 0 1-2-2V3a2 2 0 0 1 2-2zm0 4v13h10V5z"/></svg>123-555-0178</li>
        <li><svg viewBox="0 0 24 24"><path d="M2 5h20v14H2zm2 2v.5l8 5 8-5V7z"/></svg>hello@turnwell.com</li>
        <li><svg viewBox="0 0 24 24"><circle cx="12" cy="12" r="10"/></svg>www.turnwell.com</li>
      </ul>
    </div>
  </section>

  <section class="card card-back" aria-label="Appointment side">
    <div class="brand"><span class="brand-dot"></span>Turnwell Weightloss</div>
    <div class="blank-line" style="margin-top:-14px;margin-left:130px;margin-right:30px"></div>
    <p class="appt-title">Your Next Appointment is</p>
    <div class="blank-line" style="margin-top:-22px;margin-left:250px"></div>
    <div class="field"><span class="field-label">Name:</span><span class="field-fill"></span></div>
    <div class="field"><span class="field-label">Date:</span><span class="field-fill"></span></div>
    <div class="field"><span class="field-label">Time:</span><span class="field-fill"></span><span class="field-unit">AM</span><span class="field-fill"></span><span class="field-unit">PM</span></div>
    <p class="notice">If unable to keep appointment, kindly give 24hrs notice.</p>
  </section>

</main>
</body>
</html>
```